Help design website for "Brightwater Civic Advisors" to advance the common good

Here is the Google doc link that lays out the design:

https://files.plumrivet.example/sheet/d/7QmTzR2wLx9KpVbN4hJcY8sEaUoFdG3iXkMnPq5rWt6/edit?usp=sharing

Here is the Google drive folder with the logos and photos: https://vault.plumrivet.example/open?id=4HkWp9LzQe2TxRvN8mBaYc3DsUoJfG6

The testimonials are being gathered and will be shared by Friday, 1/4.

The winner will also have to migrate the coding files to my hosting site.

Thank you for your help! Looking forward to seeing your designs.

Target Market(s)

Prospective clients

Industry/Entity Type

Non Profit

Coding

Coded - Design and coding required

Number of Pages Required

5+ page

Requirements
Must have
• Noted in the Google doc regarding layout.
Nice to have

```html
<!DOCTYPE html>
<html lang="en">
<head>
<meta charset="utf-8">
<title>Brightwater Civic Advisors</title>
<link href="https://fonts.googleapis.com/css2?family=Montserrat:wght@400;500;600;700&family=Open+Sans:ital,wght@0,400;0,600;1,400&display=swap" rel="stylesheet">
<style>
:root{
  --blue:#2f7fd1;
  --blue-dark:#1f5fa8;
  --ink:#2b2d33;
  --text:#555a63;
  --muted:#8b9099;
  --pale:#eef5fc;
  --line:#e3e6ea;
  --white:#ffffff;
}
*{box-sizing:border-box;margin:0;padding:0}
html,body{width:1200px;height:4986px;overflow:hidden}
body{position:relative;background:var(--white);font-family:"Open Sans",Arial,sans-serif;color:var(--text)}
.abs{position:absolute}
.heading{font-family:"Montserrat",Arial,sans-serif;font-weight:400;font-size:38px;letter-spacing:1px;color:var(--ink);text-align:center;text-transform:uppercase}
.heading .accent{color:var(--blue)}
.btn{display:inline-block;background:var(--blue);color:var(--white);font-family:"Montserrat",Arial,sans-serif;font-weight:600;font-size:15px;letter-spacing:.5px;text-transform:uppercase;border-radius:30px;padding:15px 30px}

/* nav */
.topbar{left:0;top:0;width:1200px;height:115px;background:var(--white)}
.topnav{left:112px;top:46px;display:flex;gap:36px;font-family:"Montserrat",Arial,sans-serif;font-size:17px;font-weight:500;color:var(--ink)}
.topnav .current{color:var(--blue)}
.brand{display:flex;align-items:center;gap:14px}
.brand-mark{width:40px;height:40px;background:var(--blue);flex:none}
.brand-name{font-family:"Montserrat",Arial,sans-serif;font-weight:500;text-transform:uppercase;letter-spacing:3px;line-height:1.1;color:var(--ink)}
.topbar .brand{position:absolute;right:110px;top:24px}
.topbar .brand-name{font-size:17px;width:190px}

/* hero */
.hero{left:0;top:115px;width:1200px;height:650px;background:linear-gradient(180deg,#1d2a3e 0%,#3d4a63 38%,#a8633a 62%,#2a2630 100%);clip-path:polygon(0 0,100% 0,100% 100%,0 82%)}
.hero .brand{position:absolute;left:112px;top:150px}
.hero .brand-mark{width:110px;height:110px}
.hero .brand-name{font-size:46px;color:var(--white);width:520px;letter-spacing:2px}
.hero-tag{left:112px;top:312px;font-family:"Montserrat",Arial,sans-serif;font-size:20px;color:var(--white)}
.hero .btn{position:absolute;left:112px;top:370px;padding:12px 26px;font-size:14px}
.dots{left:112px;top:478px;display:flex;gap:8px}
.dots span{width:10px;height:10px;border-radius:50%;background:rgba(255,255,255,.6)}
.dots span:nth-child(3){background:var(--white)}
.portrait{left:680px;top:478px;width:280px;height:280px;border-radius:50%;border:8px solid var(--blue);background:radial-gradient(circle at 50% 40%,#6a5a52,#2d2a2c 70%)}

/* about */
.about-title{left:0;top:800px;width:1200px}
.about-copy{left:170px;top:878px;width:860px;text-align:center;font-size:14px;line-height:2.4}
.about-copy p{margin-bottom:8px}
.about-btn{left:0;top:1238px;width:1200px;text-align:center}

/* work */
.work-band{left:0;top:1428px;width:1200px;height:697px;background:var(--pale)}
.work-title{left:0;top:1512px;width:1200px}
.work-card{left:110px;top:1610px;width:976px;height:455px;background:var(--white);box-shadow:0 2px 12px rgba(0,0,0,.1);display:grid;grid-template-columns:repeat(3,1fr);grid-template-rows:1fr 1fr;padding:20px 20px}
.client{display:flex;align-items:center;justify-content:center;gap:12px;font-family:"Montserrat",Arial,sans-serif;font-weight:700;font-size:19px;color:var(--ink);text-align:center;line-height:1.2;border-right:1px solid var(--line)}
.client:nth-child(3n){border-right:none}
.client:nth-child(-n+3){border-bottom:1px solid var(--line)}
.client .mark{width:34px;height:34px;flex:none;background:var(--blue)}
.client .mark.round{border-radius:50%;background:var(--ink)}

/* services */
.svc-title{left:0;top:2186px;width:1200px}
.svc-grid{left:110px;top:2284px;width:976px;display:grid;grid-template-columns:repeat(3,1fr);gap:27px 30px}
.svc{height:272px;background:var(--white);box-shadow:0 2px 10px rgba(0,0,0,.12);position:relative}
.svc-photo{height:180px;background:linear-gradient(135deg,#4b4f5a,#8a7d72)}
.svc-name{padding:18px 20px;font-size:15px;line-height:1.6;color:var(--ink);width:230px}
.svc-icon{position:absolute;right:14px;top:150px;width:60px;height:60px;background:var(--white);border-radius:4px;display:flex;align-items:center;justify-content:center}
.svc.active{background:var(--blue)}
.svc.active .svc-name{color:var(--white)}
.svc.active .svc-icon{background:var(--blue)}

/* testimonial */
.quote{left:110px;top:2915px;width:976px;height:183px;background:#3a3c40;padding:30px 70px;text-align:center}
.quote p{font-style:italic;font-size:13px;line-height:2;color:#d6d8dc}
.quote .who{margin-top:14px;font-style:normal;font-size:13px;color:#d6d8dc}
.quote .who b{color:var(--blue);font-family:"Montserrat",Arial,sans-serif;font-size:16px}
.quote-mark{left:1040px;top:3060px}

/* media */
.media-title{left:0;top:3188px;width:1200px}
.media-sub{left:0;top:3255px;width:1200px;text-align:center;font-size:14px;color:var(--muted)}
.media-grid{left:110px;top:3320px;width:976px;display:grid;grid-template-columns:471px 468px;gap:26px 37px}
.media{height:289px;position:relative;background:linear-gradient(160deg,#3f4654,#1e2229)}
.media.red{background:linear-gradient(160deg,#8a1a1f,#4a0c10)}
.media.green{background:linear-gradient(160deg,#4a5d46,#2a3228)}
.media-cap{position:absolute;left:40px;bottom:22px;width:330px;color:var(--white);font-size:15px;line-height:1.5}
.media-cap time{display:inline-block;margin-top:8px;font-size:13px;color:#b9d6f5;border-bottom:1px solid #b9d6f5}
.media-icon{position:absolute;right:20px;bottom:30px;width:40px;height:40px;border-radius:50%;background:var(--blue);display:flex;align-items:center;justify-content:center}

/* rates */
.rates-mark{left:455px;top:4365px;opacity:.08}
.rates-title{left:0;top:4360px;width:1200px}
.rates-copy{left:300px;top:4432px;width:600px;text-align:center;font-size:16px;line-height:2;color:var(--muted)}
.rates-btn{left:0;top:4518px;width:1200px;text-align:center}

/* footer */
.footer-shape{left:0;top:4590px}
.footer-social{left:1012px;top:4822px;display:flex;gap:12px}
.footer-social span{width:16px;height:16px;background:var(--white);border-radius:3px}
.footer .brand{position:absolute;left:112px;top:4860px}
.footer .brand-mark{width:60px;height:60px}
.footer .brand-name{font-size:22px;color:var(--white);width:310px}
.footer-nav{right:112px;top:4868px;display:flex;gap:14px;font-family:"Montserrat",Arial,sans-serif;font-weight:600;font-size:16px;color:var(--white)}
.footer-copy{right:112px;top:4908px;font-size:12px;color:#c8cbd0}
</style>
</head>
<body>

<header class="abs topbar">
  <nav class="abs topnav"><span class="current">About</span><span>Services &amp; Testimonials</span><span>Media &amp; Impact</span><span>Contact</span></nav>
  <div class="brand"><span class="brand-mark"></span><span class="brand-name">Brightwater Civic Advisors</span></div>
</header>

<section class="abs hero" role="img" aria-label="City skyline at sunset along the river">
  <div class="brand"><span class="brand-mark"></span><span class="brand-name">Brightwater Civic Advisors</span></div>
  <p class="abs hero-tag">Sed ut perspiciatis unde omnis iste natus error sit voluptatem</p>
  <span class="btn">Read more</span>
  <div class="abs dots"><span></span><span></span><span></span><span></span></div>
</section>
<svg class="abs" style="left:0;top:115px" width="1200" height="660" aria-hidden="true">
  <line x1="0" y1="533" x2="1200" y2="650" stroke="#2f7fd1" stroke-width="5"/>
</svg>
<div class="abs portrait" role="img" aria-label="Portrait of the founder"></div>

<section>
  <h2 class="abs heading about-title">About</h2>
  <div class="abs about-copy">
    <p>Brightwater Civic Advisors supports nonprofit organizations and educational institutions to carry out their missions to benefit the wider community. Founder Renata Osei is an educator with a 22-year record of demonstrated achievement and leadership roles in nonprofit and educational institutions. Most recently, she served as Associate Dean of Students at Lakeview University and Director of the Lakeview Community Service Center.</p>
    <p>She has also significantly and consistently increased the number of program applicants, volunteers, and community partnerships through innovative programming, improved evaluation, targeted recruitment, marketing and communications.</p>
    <p>Renata is a native of the city and has also lived in Tokyo, Boston, San Francisco, and Washington, DC. She received her bachelor of arts from Northfield College in Northfield, MN and her masters in education from Eastbrook University.</p>
  </div>
  <div class="abs about-btn"><span class="btn">Read more info</span></div>
</section>

<section>
  <div class="abs work-band"></div>
  <svg class="abs" style="left:0;top:1428px" width="1200" height="200" aria-hidden="true">
    <polygon points="0,0 120,0 0,90" fill="#e2edf9"/>
    <polygon points="1200,0 1080,0 1200,90" fill="#e2edf9"/>
  </svg>
  <h2 class="abs heading work-title">Work <span class="accent">History</span></h2>
  <div class="abs work-card">
    <div class="client"><span class="mark"></span>Lakeview Community<br>Service Center</div>
    <div class="client"><span class="mark round"></span>Harbor Fellows</div>
    <div class="client"><span class="mark"></span>Summit Bay Area</div>
    <div class="client"><span class="mark"></span>Civic Youth Schools</div>
    <div class="client"><span class="mark round"></span>ServeNation Corps</div>
    <div class="client"><span class="mark"></span>Teaching Exchange</div>
  </div>
</section>

<section>
  <h2 class="abs heading svc-title">Services &amp; <span class="accent">Testimonials</span></h2>
  <div class="abs svc-grid">
    <div class="svc active"><div class="svc-photo" role="img" aria-label="Staff group photo at a training"></div><div class="svc-icon"><svg width="30" height="30"><circle cx="15" cy="10" r="6" fill="#fff"/><rect x="5" y="18" width="20" height="10" rx="4" fill="#fff"/></svg></div><p class="svc-name">Staff Professional Development</p></div>
    <div class="svc"><div class="svc-photo" role="img" aria-label="Students gathered at a partner event"></div><div class="svc-icon"><svg width="30" height="30"><path d="M4 15h22M15 4v22" stroke="#2f7fd1" stroke-width="3"/></svg></div><p class="svc-name">Community Partnership Development</p></div>
    <div class="svc"><div class="svc-photo" role="img" aria-label="Workshop room with participants"></div><div class="svc-icon"><svg width="30" height="30"><rect x="4" y="14" width="5" height="12" fill="#2f7fd1"/><rect x="12" y="8" width="5" height="18" fill="#2f7fd1"/><rect x="20" y="4" width="5" height="22" fill="#2f7fd1"/></svg></div><p class="svc-name">Group Facilitation &amp;Leadership Training</p></div>
    <div class="svc"><div class="svc-photo" role="img" aria-label="Large group of program participants"></div><div class="svc-icon"><svg width="30" height="30"><rect x="3" y="5" width="24" height="16" fill="none" stroke="#2f7fd1" stroke-width="3"/><path d="M10 27h10" stroke="#2f7fd1" stroke-width="3"/></svg></div><p class="svc-name">Program Design, Implementation, &amp; Evaluation</p></div>
    <div class="svc"><div class="svc-photo" role="img" aria-label="Speaker at a podium"></div><div class="svc-icon"><svg width="30" height="30"><rect x="4" y="6" width="22" height="20" fill="none" stroke="#2f7fd1" stroke-width="3"/><path d="M4 12h22" stroke="#2f7fd1" stroke-width="3"/></svg></div><p class="svc-name">Event Planning</p></div>
    <div class="svc"><div class="svc-photo" role="img" aria-label="Presenter beside a projected slide"></div><div class="svc-icon"><svg width="30" height="30"><rect x="4" y="4" width="22" height="22" fill="none" stroke="#2f7fd1" stroke-width="3"/><path d="M9 18l5-5 4 4 5-6" fill="none" stroke="#2f7fd1" stroke-width="3"/></svg></div><p class="svc-name">Strategic Planning &amp; Visioning</p></div>
  </div>
</section>

<section class="abs quote">
  <p>"Renata has an uncanny ability to combine social change theory and real world practice in truly compelling ways. For five years at Lakeview University, I saw first hand how she inspired legions of students, created innovative programs, and transformed relationships with community stakeholders. Best of all, she did it with integrity, smarts, enthusiasm and a warm, infectious spirit."</p>
  <p class="who"><b>- Daniel Hartwell, VP</b> Chief Content Officer, Brookfield Community Media</p>
</section>
<svg class="abs quote-mark" width="56" height="44" aria-hidden="true"><rect x="0" y="0" width="22" height="20" fill="#2f7fd1"/><path d="M6 20h16l-10 22H4z" fill="#2f7fd1"/><rect x="30" y="0" width="22" height="20" fill="#2f7fd1"/><path d="M36 20h16l-10 22h-8z" fill="#2f7fd1"/></svg>

<section>
  <h2 class="abs heading media-title">Media &amp; <span class="accent">Impact</span></h2>
  <p class="abs media-sub">Here is the media coverage for the programs and events that Renata oversaw.</p>
  <div class="abs media-grid">
    <div class="media" role="img" aria-label="Students in a classroom discussion"><p class="media-cap">Dana Whitfield leads students in Riverside day of action on global forum's last day<br><time>October 2016</time></p><span class="media-icon"><svg width="18" height="18"><rect x="2" y="2" width="14" height="14" fill="none" stroke="#fff" stroke-width="2"/></svg></span></div>
    <div class="media" role="img" aria-label="Students gathered in a gymnasium"><p class="media-cap">Lakeview Open Exchange Program Celebrates First Year<br><time>May 2016</time></p><span class="media-icon"><svg width="18" height="18"><rect x="2" y="2" width="14" height="14" fill="none" stroke="#fff" stroke-width="2"/></svg></span></div>
    <div class="media green" role="img" aria-label="Volunteers working in a city garden"><p class="media-cap">Dana Whitfield joins Day of Action volunteering events in the city<br><time>April 2016</time></p><span class="media-icon"><svg width="18" height="18"><path d="M5 3l10 6-10 6z" fill="#fff"/></svg></span></div>
    <div class="media green" role="img" aria-label="Young volunteers outdoors in a park"><p class="media-cap">Hundreds of young volunteers think globally, act locally<br><time>October 2016</time></p><span class="media-icon"><svg width="18" height="18"><path d="M5 3l10 6-10 6z" fill="#fff"/></svg></span></div>
    <div class="media" role="img" aria-label="Speaker on stage under a spotlight"><p class="media-cap">"Dreams, Ideas, and You" - A conversation with Renata Osei on how to get involved<br><time>February 2016</time></p><span class="media-icon"><svg width="18" height="18"><rect x="6" y="2" width="6" height="10" rx="3" fill="#fff"/><path d="M9 13v4" stroke="#fff" stroke-width="2"/></svg></span></div>
    <div class="media red" role="img" aria-label="Dark red event banner"><p class="media-cap">Riverside Mercy, Spring Day of Service<br><time>January 2016</time></p><span class="media-icon"><svg width="18" height="18"><rect x="6" y="2" width="6" height="10" rx="3" fill="#fff"/><path d="M9 13v4" stroke="#fff" stroke-width="2"/></svg></span></div>
  </div>
</section>

<section>
  <svg class="abs rates-mark" width="290" height="290" aria-hidden="true"><rect x="0" y="0" width="290" height="290" fill="#2f7fd1"/></svg>
  <h2 class="abs heading rates-title">Rates</h2>
  <p class="abs rates-copy">Depending on the service requested, Renata offers an hourly rate, a package rate, or a retainer fee based on the scope and complexity of the project.</p>
  <div class="abs rates-btn"><span class="btn">Book a complimentary consultation</span></div>
</section>

<footer class="footer">
  <svg class="abs footer-shape" width="1200" height="396" aria-hidden="true">
    <polygon points="0,0 600,170 1200,0 1200,396 0,396" fill="#2b2d33"/>
    <polyline points="0,0 600,170 1200,0" fill="none" stroke="#2f7fd1" stroke-width="5"/>
  </svg>
  <div class="abs footer-social"><span></span><span></span><span></span></div>
  <div class="brand"><span class="brand-mark"></span><span class="brand-name">Brightwater Civic Advisors</span></div>
  <nav class="abs footer-nav"><span>About</span><span>/</span><span>Services &amp; Testimonials</span><span>/</span><span>Media &amp; Impact</span><span>/</span><span>Contact</span></nav>
  <p class="abs footer-copy">Copyright © 2016. Brightwater Civic Advisors. All Right Reserved</p>
</footer>

</body>
</html>
```